MRT Property - Business Cards

Looking for a business card & general letterhead, signage etc design for our new logo.

Colours:
000a20
0056a2
00b5ef
0088ce
68cef2

Fonts:
Poppins
Karla

Please keep look and feel of new brand - example in the zip package I sent.

```html
<!DOCTYPE html>
<html lang="en">
<head>
<meta charset="utf-8">
<title>MRT Property – Business Cards</title>
<link rel="stylesheet" href="https://fonts.googleapis.com/css2?family=Poppins:wght@600;700&family=Karla:wght@400;700&display=swap">
<style>
  :root {
    --ink: #000a20;
    --navy: #0056a2;
    --cyan: #00b5ef;
    --mid-blue: #0088ce;
    --sky: #68cef2;
    --card: #f5f5f5;
    --backdrop: #e4e6ea;
    --text: #2a2f3a;
  }
  * { box-sizing: border-box; margin: 0; padding: 0; }
  html, body { width: 1200px; height: 900px; overflow: hidden; }
  body {
    background: var(--backdrop);
    display: flex;
    flex-direction: column;
    align-items: center;
    justify-content: center;
    gap: 60px;
    font-family: "Karla", sans-serif;
  }
  .card {
    width: 600px;
    height: 343px;
    background: var(--card);
    border-radius: 26px;
    box-shadow: 0 6px 18px rgba(0, 10, 32, 0.18);
    position: relative;
  }
  .brand {
    display: flex;
    align-items: center;
    gap: 14px;
    font-family: "Poppins", sans-serif;
    font-weight: 700;
    color: var(--navy);
    white-space: nowrap;
  }
  .brand-mark {
    background: var(--cyan);
    flex: none;
  }
  /* front */
  .card-front {
    display: flex;
    align-items: center;
    justify-content: center;
  }
  .card-front .brand { font-size: 58px; }
  .card-front .brand-mark { width: 40px; height: 40px; }
  /* back */
  .card-back {
    display: flex;
    align-items: center;
    padding: 0 46px;
  }
  .card-back .brand { font-size: 30px; width: 250px; gap: 10px; }
  .card-back .brand-mark { width: 22px; height: 22px; }
  .divider {
    width: 2px;
    height: 170px;
    background: var(--sky);
    margin: 0 30px 0 10px;
  }
  .details { color: var(--text); font-size: 17px; line-height: 1.5; }
  .holder-name {
    font-weight: 700;
    color: var(--navy);
    font-size: 24px;
    letter-spacing: 0.04em;
    text-transform: uppercase;
    line-height: 1.1;
  }
  .holder-role { margin-bottom: 8px; }
  .contact-row { display: flex; align-items: center; gap: 8px; }
  .contact-row svg { width: 15px; height: 15px; fill: var(--navy); flex: none; }
  .address { margin-top: 4px; }
</style>
</head>
<body>
  <section class="card card-front">
    <div class="brand"><span class="brand-mark"></span>MRT Property</div>
  </section>

  <section class="card card-back">
    <div class="brand"><span class="brand-mark"></span>MRT Property</div>
    <div class="divider"></div>
    <div class="details">
      <p class="holder-name">Daniel Reeve</p>
      <p class="holder-role">Managing Director</p>
      <p class="contact-row">
        <svg viewBox="0 0 24 24" aria-hidden="true"><path d="M6.6 10.8a15 15 0 0 0 6.6 6.6l2.2-2.2a1 1 0 0 1 1-.25 11.4 11.4 0 0 0 3.6.57 1 1 0 0 1 1 1V20a1 1 0 0 1-1 1A17 17 0 0 1 3 4a1 1 0 0 1 1-1h3.5a1 1 0 0 1 1 1c0 1.25.2 2.45.57 3.57a1 1 0 0 1-.25 1z"/></svg>
        123 456 789
      </p>
      <p class="contact-row">
        <svg viewBox="0 0 24 24" aria-hidden="true"><path d="M3 5h18a1 1 0 0 1 1 1v12a1 1 0 0 1-1 1H3a1 1 0 0 1-1-1V6a1 1 0 0 1 1-1zm1 2.2V17h16V7.2l-8 5.3z"/></svg>
        info@mrtproperty.com
      </p>
      <p class="contact-row">
        <svg viewBox="0 0 24 24" aria-hidden="true"><circle cx="12" cy="12" r="9" fill="none" stroke="currentColor"/><path d="M12 2a10 10 0 1 0 0 20 10 10 0 0 0 0-20zm0 2c1.4 1.5 2.3 4.6 2.3 8s-.9 6.5-2.3 8c-1.4-1.5-2.3-4.6-2.3-8S10.6 5.5 12 4zM4.1 11h3.9a16 16 0 0 0 0 2H4.1a8 8 0 0 1 0-2zm11.9 0h3.9a8 8 0 0 1 0 2H16a16 16 0 0 0 0-2z"/></svg>
        www.mrtproperty.com
      </p>
      <p class="address">Your address, City<br>State, Zip 1234</p>
    </div>
  </section>
</body>
</html>
```